Church Website with Home Page and Member Sermon Library

I am in need of an updated design for our church website. This will include 4 pages (outlined below). We are a conservative, evangelical, Christian church. The site should be modern and clean, while still reflecting our conservative values. I already have a logo for our church, and I want the site to incorporate the logo, and match the logo/branding. Stock photos are allowed if needed, but I have uploaded some images of our church and would prefer those images to be used if possible. Any stock photos used should not include any people in the photos (scenery, nature, buildings, animals, etc. are fine).

The site will need 4 pages: Home, Support Us (Donate), Login, and Recording Library.

Page 1: Home
The home page should include the following sections:

- Navigation: Should include links to each section of the home page plus a "listen live" link which will take the user to a live-streaming site and a "support us" link which will take the user to a support/donate page.

- Announcements: Can be either a banner or some other design, but there needs to be some way for us to post announcements for visitors to see. I'm open for creative ideas in this section, but would like it not to take up a lot of room on the page.

- About Us: Should include address, service times (see attached document), and information about the church.

- Pastor Bio: A section that introduces our pastor and gives a short bio about our pastor. Would like this section to include a picture of our pastor. Somewhere in this section I would like to include this Bible reference: "And I will give you pastors according to mine heart, which shall feed you with knowledge and understanding. Jer 3:15 LPW"

- Articles of Faith (What We Believe): This should include several sub-sections each with a heading, body, and possibly 1 or more scripture references. I have attached a document to the brief that includes our articles of faith. Feel free to be creative with this section in how you lay these out and format them.

- Support Us: A small section that explains what kind of support someone can give and a link to a donation page. The link can say something like "Support Us" or "Donate Now".

- Contact form: A contact form that allows the visitor to send us a message. The contact form should ask for name, email, phone, and message.

- Footer: A footer that will be displayed on all pages of the site. This should include at a minimum a link to the home page (or a link to each individual section in the home page if you prefer), a link to "listen live", a link to "support us", a link to "contact us" (or you can put the contact form directly in the footer if you prefer), the address, and a "member login" link.

Page 2: Support Us
The donation page should include a form the visitor can fill out to make a donation. We will embed a third party form later. For this design, please just mock out the design with a basic form asking for name, phone, and email.

Page 3: Login
The recording library (detailed below) will require members to login with a shared numeric code before accessing the page. We need a design for a login screen. The screen should include navigation/footer just like all other pages, but the body of the login page will consist only of a form that asks the user to enter the access code and then a "login" button.

Page 4: Recording Library

The library page is a member-only page that will require a shared, numeric pass code to access. On this page, members will be able to access a filterable list of past sermons. The page by default should display most recent sermons, but should also include a search form that allows the member to filter the sermon list to find a particular sermon. The search form should allow the user to select a filter type (e.g. Speaker name, date, event, etc.) and type in a value to search. They should be able to add multiple filters and remove filters that have been added. Each sermon that is displayed in the result list should include basic information such as title, date, speaker, tags, etc. along with a download icon, and an embedded audio player where they can click a play button to stream it on-demand. Each sermon should also have clickable tags associated with it that can be used to find related sermons.
Updates

I have uploaded several images of our church. Feel free to incorporate these into your design if possible.

Target Market(s)

Church Members

Industry/Entity Type

Religion

Number of Pages Required

4 page

Font styles to use
Sans Serif

Colors

Designer to choose colors to be used in the design.

Requirements
Must have
• Must incorporate the logo (attached)
Nice to have
• Would like the design to incorporate pictures of our church (attached) instead of stock photos if possible.
Should not have
• Please avoid an overly cluttered design. Stock photos used should not include any people in the photos.

```html
<!DOCTYPE html>
<html lang="en">
<head>
<meta charset="utf-8">
<title>Library – Grace Hill Chapel</title>
<link href="https://fonts.googleapis.com/css2?family=Cinzel:wght@400;700&family=Montserrat:wght@400;500&display=swap" rel="stylesheet">
<style>
:root{
  --green:#7eaa68;
  --ink:#1d1d1d;
  --muted:#4a4a4a;
  --rule:#dcdcdc;
  --field:#f6f6f6;
  --field-border:#d6d6d6;
  --footer:#2e2e2e;
  --footer-rule:#3d3d3d;
  --white:#ffffff;
}
*{margin:0;padding:0;box-sizing:border-box}
html,body{width:706px;height:1200px;overflow:hidden;background:var(--white)}
body{position:relative;font-family:'Montserrat',sans-serif;color:var(--ink)}
h1,h2,h3{font-weight:400}
.abs{position:absolute}

.hero{left:0;top:0;width:706px;height:267px;
  background:radial-gradient(ellipse at 15% 10%,#fbf3ec 0%,rgba(251,243,236,.6) 30%,rgba(0,0,0,0) 60%),
  linear-gradient(160deg,#e9c9ad 0%,#cf925f 35%,#b8703f 60%,#9b5a33 80%,#6d4533 100%)}
.hero-fade{left:0;top:0;width:706px;height:100px;background:linear-gradient(#fff 0%,rgba(255,255,255,.7) 45%,rgba(255,255,255,0) 100%)}
.brand{left:72px;top:30px;width:104px;text-align:center;font-family:'Cinzel',serif;color:var(--green);font-size:12px;line-height:14px;letter-spacing:1px;white-space:nowrap}
.brand small{display:block;font-size:6px;letter-spacing:4px;line-height:9px}
.nav{top:31px;right:175px;display:flex;gap:15px;font-size:7.6px;font-weight:500}
.nav a{white-space:nowrap;color:var(--ink);text-decoration:none}
.btn{display:flex;align-items:center;justify-content:center;background:var(--green);color:var(--white);font-family:'Cinzel',serif;font-size:9px;text-decoration:none;white-space:nowrap}
.btn-nav{left:547px;top:25px;width:58px;height:21px}
.page-title{left:0;width:706px;top:142px;text-align:center;font-family:'Cinzel',serif;font-size:32px;letter-spacing:2px;color:#111}
.title-rule{left:305px;top:186px;width:95px;height:1.5px;background:#111}
.title-rule-thin{left:329px;top:190.5px;width:47px;height:.5px;background:#111}

.section-title{font-family:'Cinzel',serif;color:var(--ink);letter-spacing:1.3px;white-space:nowrap}
.sermons-title{left:102px;top:293px;font-size:13px}
.rule{height:1px;background:var(--rule)}
.filter-label{font-size:7.4px;color:var(--muted);white-space:nowrap}
.field{display:flex;align-items:center;justify-content:space-between;padding:0 7px;border:1px solid var(--field-border);background:var(--field);font-size:8px;font-weight:500;color:#333;white-space:nowrap}
.field svg{width:6px;height:4px}
.field.input{background:var(--white);font-weight:400}
.btn-add{font-family:'Montserrat',sans-serif;font-size:7.6px;font-weight:500;gap:4px}
.active-filters{left:101px;top:357px;display:flex;align-items:center;gap:6px}
.chip{height:17px;padding:0 6px 0 8px;border-radius:9px;background:#eef4ea;border:1px solid #cfe0c5;display:flex;align-items:center;gap:5px;font-size:7px;color:#333;white-space:nowrap}
.chip b{font-weight:500}
.chip .remove{font-size:9px;line-height:1;color:#5b8a45}
.clear-all{font-size:7px;color:#5b8a45;text-decoration:underline;margin-left:4px}

.card{width:245px;height:152px;overflow:hidden;color:var(--white)}
.card-photo{position:absolute;inset:0;background:linear-gradient(180deg,#4d5a45 0%,#a7b39e 28%,#8d9b84 50%,#4a6a3b 75%,#2c4d21 100%)}
.card-photo.warm{background:linear-gradient(180deg,#6b6048 0%,#b2a890 30%,#8c9a80 52%,#4a6a3b 75%,#2c4d21 100%)}
.download{position:absolute;top:12px;right:11px;display:flex;align-items:center;gap:5px;font-size:7px}
.download svg{width:8px;height:8px}
.play{position:absolute;left:102px;top:55px;width:42px;height:42px;border-radius:50%;border:1.5px solid var(--green);background:rgba(255,255,255,.55);display:flex;align-items:center;justify-content:center}
.play svg{width:11px;height:12px;margin-left:2px}
.date{position:absolute;left:14px;top:108px;display:flex;align-items:center;gap:3px;font-size:6.8px}
.date svg{width:6px;height:6px}
.card-title{position:absolute;left:14px;top:119px;font-family:'Cinzel',serif;font-weight:700;font-size:9.3px;letter-spacing:1px;white-space:nowrap}
.speaker{position:absolute;left:14px;top:133px;display:flex;align-items:center;gap:5px;font-size:7px}
.avatar{width:13px;height:13px;border-radius:50%;background:#c9bcae;border:1px solid #fff}

.tags-title{left:103px;top:901px;font-size:10px}
.tags{left:102px;top:927px;width:515px;display:flex;flex-wrap:wrap;gap:7px 6px}
.tag{height:20px;padding:0 9px;border:1px solid #dadada;border-radius:10px;display:flex;align-items:center;font-size:7.6px;letter-spacing:.7px;color:#444;white-space:nowrap}

.footer{left:0;top:1012px;width:706px;height:188px;background:var(--footer)}
.footer-brand{left:100px;top:1088px;width:128px;text-align:center;font-family:'Cinzel',serif;color:var(--green);font-size:16px;line-height:18px;letter-spacing:1.5px;white-space:nowrap}
.footer-brand small{display:block;font-size:7px;letter-spacing:5px;line-height:11px}
.footer-head{font-family:'Cinzel',serif;font-size:11px;letter-spacing:1.2px;color:#e6e6e6}
.contact-row{display:flex;gap:4px;font-size:6.6px;line-height:8px;color:#cfcfcf;white-space:nowrap}
.contact-row svg{width:6px;height:6px;flex:none;margin-top:1px}
.donation-text{left:464px;top:1082px;width:140px;font-size:6.8px;line-height:11px;color:#cfcfcf}
.btn-footer{left:464px;top:1113px;width:59px;height:22px}
.footer-rule{left:0;top:1165px;width:706px;height:1px;background:var(--footer-rule)}
.copyright{left:104px;top:1179px;font-size:7px;color:#dcdcdc;white-space:nowrap}
.social{left:540px;top:1180px;display:flex;gap:9px}
.social span{width:7px;height:7px;border-radius:50%;background:#e0e0e0}
</style>
</head>
<body>

<header>
  <div class="abs hero" role="img" aria-label="Photo of wooden church pews in soft light"></div>
  <div class="abs hero-fade"></div>
  <div class="abs brand">GRACE HILL<small>CHAPEL</small></div>
  <nav class="abs nav">
    <a href="#">Home</a>
    <a href="#">About</a>
    <a href="#">Our Pastor</a>
    <a href="#">Articles Of Faith</a>
    <a href="#">Listen Live</a>
    <a href="#">Support Us</a>
  </nav>
  <a href="#" class="abs btn btn-nav">DONATE</a>
  <h1 class="abs page-title">LIBRARY</h1>
  <div class="abs title-rule"></div>
  <div class="abs title-rule-thin"></div>
</header>

<main>
  <h2 class="abs section-title sermons-title">LIST OF PAST SERMONS</h2>
  <div class="abs rule" style="left:101px;top:313px;width:504px"></div>

  <form class="sermon-search">
    <span class="abs filter-label" style="left:101px;top:333px">Filter by:</span>
    <div class="abs field" style="left:142px;top:326px;width:86px;height:22px">Speaker
      <svg viewBox="0 0 6 4"><path d="M0 0h6L3 4z" fill="#333"/></svg></div>
    <div class="abs field input" style="left:234px;top:326px;width:200px;height:22px">Mara Ellison</div>
    <a href="#" class="abs btn btn-add" style="left:440px;top:326px;width:72px;height:22px">+ Add filter</a>
    <a href="#" class="abs btn btn-add" style="left:518px;top:326px;width:87px;height:22px;background:#4f7d3c">Search</a>

    <div class="abs active-filters">
      <span class="filter-label">Active:</span>
      <span class="chip"><b>Speaker:</b> Mara Ellison <span class="remove">×</span></span>
      <span class="chip"><b>Date:</b> 01/10/2022 - 15/02/2023 <span class="remove">×</span></span>
      <span class="chip"><b>Event:</b> Sunday Service <span class="remove">×</span></span>
      <a href="#" class="clear-all">Clear all</a>
    </div>
  </form>

  <svg width="0" height="0" style="position:absolute">
    <defs>
      <symbol id="i-dl" viewBox="0 0 10 10"><path d="M5 1v5.5M2.5 4.5 5 7l2.5-2.5M1 8.8h8" fill="none" stroke="#8dbb74" stroke-width="1.1"/></symbol>
      <symbol id="i-cal" viewBox="0 0 8 8"><rect x=".7" y="1.3" width="6.6" height="6" fill="none" stroke="#fff" stroke-width=".8"/><path d="M.7 3.2h6.6M2.3.4v1.6M5.7.4v1.6" stroke="#fff" stroke-width=".8"/></symbol>
      <symbol id="i-play" viewBox="0 0 11 12"><path d="M0 0l11 6-11 6z" fill="#fff"/></symbol>
    </defs>
  </svg>

  <article class="abs card" style="left:101px;top:384px">
    <div class="card-photo" role="img" aria-label="Photo of a minister reading in the sanctuary"></div>
    <div class="download">Download <svg><use href="#i-dl"/></svg></div>
    <div class="play"><svg><use href="#i-play"/></svg></div>
    <div class="date"><svg><use href="#i-cal"/></svg>Fab 12, 2023</div>
    <h3 class="card-title">ULLAMCORPER FACILISI EGESTAS</h3>
    <div class="speaker"><span class="avatar"></span>by:&nbsp; Mara Ellison</div>
  </article>
  <article class="abs card" style="left:360px;top:384px">
    <div class="card-photo" role="img" aria-label="Photo of a minister with a Bible by a window"></div>
    <div class="download">Download <svg><use href="#i-dl"/></svg></div>
    <div class="play"><svg><use href="#i-play"/></svg></div>
    <div class="date"><svg><use href="#i-cal"/></svg>Fab 12, 2023</div>
    <h3 class="card-title">ULLAMCORPER FACILISI EGESTAS</h3>
    <div class="speaker"><span class="avatar"></span>by:&nbsp; Mara Ellison</div>
  </article>
  <article class="abs card" style="left:101px;top:550px">
    <div class="card-photo" role="img" aria-label="Photo of a minister with a Bible by a window"></div>
    <div class="download">Download <svg><use href="#i-dl"/></svg></div>
    <div class="play"><svg><use href="#i-play"/></svg></div>
    <div class="date"><svg><use href="#i-cal"/></svg>Fab 12, 2023</div>
    <h3 class="card-title">ULLAMCORPER FACILISI EGESTAS</h3>
    <div class="speaker"><span class="avatar"></span>by:&nbsp; Mara Ellison</div>
  </article>
  <article class="abs card" style="left:360px;top:550px">
    <div class="card-photo warm" role="img" aria-label="Photo of a minister preaching from an open book"></div>
    <div class="download">Download <svg><use href="#i-dl"/></svg></div>
    <div class="play"><svg><use href="#i-play"/></svg></div>
    <div class="date"><svg><use href="#i-cal"/></svg>Fab 12, 2023</div>
    <h3 class="card-title">ULLAMCORPER FACILISI EGESTAS</h3>
    <div class="speaker"><span class="avatar"></span>by:&nbsp; Mara Ellison</div>
  </article>
  <article class="abs card" style="left:101px;top:716px">
    <div class="card-photo" role="img" aria-label="Photo of a minister reading in the sanctuary"></div>
    <div class="download">Download <svg><use href="#i-dl"/></svg></div>
    <div class="play"><svg><use href="#i-play"/></svg></div>
    <div class="date"><svg><use href="#i-cal"/></svg>Fab 12, 2023</div>
    <h3 class="card-title">ULLAMCORPER FACILISI EGESTAS</h3>
    <div class="speaker"><span class="avatar"></span>by:&nbsp; Mara Ellison</div>
  </article>
  <article class="abs card" style="left:360px;top:716px">
    <div class="card-photo" role="img" aria-label="Photo of a minister with a Bible by a window"></div>
    <div class="download">Download <svg><use href="#i-dl"/></svg></div>
    <div class="play"><svg><use href="#i-play"/></svg></div>
    <div class="date"><svg><use href="#i-cal"/></svg>Fab 12, 2023</div>
    <h3 class="card-title">ULLAMCORPER FACILISI EGESTAS</h3>
    <div class="speaker"><span class="avatar"></span>by:&nbsp; Mara Ellison</div>
  </article>

  <div class="abs rule" style="left:101px;top:886px;width:504px"></div>
  <h2 class="abs section-title tags-title">RELATED SERMONS TAG</h2>
  <div class="abs tags">
    <a class="tag">Ullamcorper facilis</a>
    <a class="tag">eu id tempo</a>
    <a class="tag">in consectetur leo</a>
    <a class="tag">elementum gravida</a>
    <a class="tag">entum gravida</a>
    <a class="tag">in consectetur leo</a>
    <a class="tag">elementum gravida</a>
    <a class="tag">entum gravida</a>
  </div>
</main>

<footer>
  <div class="abs footer"></div>
  <div class="abs footer-brand">GRACE HILL<small>CHAPEL</small></div>

  <h2 class="abs footer-head" style="left:291px;top:1061px">CONTACT</h2>
  <div class="abs contact-row" style="left:292px;top:1087px">
    <svg viewBox="0 0 8 8"><path d="M4 7.6S1.2 4.8 1.2 3A2.8 2.8 0 0 1 6.8 3C6.8 4.8 4 7.6 4 7.6z" fill="none" stroke="#cfcfcf" stroke-width=".7"/><circle cx="4" cy="3" r="1" fill="none" stroke="#cfcfcf" stroke-width=".7"/></svg>
    <span>418 Orchard Lane, Fairview,<br>Ohio 44120</span></div>
  <div class="abs contact-row" style="left:292px;top:1111px">
    <svg viewBox="0 0 8 8"><path d="M1.5.8 3 .6l.8 1.8-1 .8a4.5 4.5 0 0 0 2 2l.8-1 1.8.8-.2 1.5C5 6.8 1.2 3 1.5.8z" fill="none" stroke="#cfcfcf" stroke-width=".6"/></svg>
    <span>+1 555 014 2290</span></div>
  <div class="abs contact-row" style="left:292px;top:1126px;letter-spacing:.6px">
    <svg viewBox="0 0 8 8"><rect x=".6" y="1.6" width="6.8" height="4.8" fill="none" stroke="#cfcfcf" stroke-width=".6"/><path d="M.6 1.8 4 4.4l3.4-2.6" fill="none" stroke="#cfcfcf" stroke-width=".6"/></svg>
    <span>gracehillchapel@mail.example</span></div>

  <h2 class="abs footer-head" style="left:464px;top:1061px">DONATION</h2>
  <p class="abs donation-text">Aliquam at commodo venenatis quis. Velit neque interdum molestie risus.</p>
  <a href="#" class="abs btn btn-footer">DONATE</a>

  <div class="abs footer-rule"></div>
  <p class="abs copyright">Copyright 2023 Grace Hill Chapel I All rights reserved</p>
  <div class="abs social" aria-label="Social links"><span></span><span></span><span></span><span></span></div>
</footer>

</body>
</html>
```